Zielgruppe
Wir sind ein Vertriebsunternehmen, mit dem Ziel die klassische Finanz und den Kryptosektor zu verbinden. Unsere Zielgruppe sind Menschen zwischn 25 - 45 Jahre. Wir sind die Communty und Vertrieb der ersten rechtkonformen STO - Plattform ( Plattform für Wertpapiere im Kryptosektor)
Diese Projekt ist Teil eines Paketes, wir bitten nur Designer mit zu machen die alle benötigten Unterlagen designen können. (siehe restliche Projekte) - Gesamtvolumen: 2300€ Preisgeld
Online-Marketing Material
2 Vorlagen Social Media - (Einladung/Event, Sprüche/Information)
Banner
Präsentationsvorlagen - min unterschiedliche 8 Vorlagenseiten /Layouts.
Landingpage Layout f. Funnelsite für Webinaranmeldung mit Platz für Formular
Newsletter Layoutvorlage
Vorlage Infografik
Broschüre / E - Book Designe
Es werden nur Vorlagen benötigt mit 'LoremSum Texten' und Musterbildern. Wir möchten von allen Vorlagen die Originaldatei, uns stehen folgende Grafikprogramme zur Verfügung:
Adobe Photoshop
Adobe Illustrator
Canva
Newsletter und Landingpage Software: mailvorra.com
Unsere Akt. Designe (Designe Alt) gefällt uns von der Idee, dennoch wünschen wir es uns moderner und edler mit ein wenig 'spaceig'. - Eben die Vereinigung von Kryptowelt und klassischer Finanz.
Schriftart: Poppins
Farben lt. Logo
Aufgabenstellung
Die Landingpage Layout f. Funnelsite für Webinaranmeldung mit Platz für Formular - Die Landingpage ersetzt nicht unsere aktuelle Website - sondern dient zur Leadgenerierung im Socialmedia Bereich.

```html
<!DOCTYPE html>
<html lang="de">
<head>
<meta charset="utf-8">
<title>Copper Lynx Investments – Webinar-Anmeldung</title>
<link href="https://fonts.googleapis.com/css2?family=Poppins:wght@400;500;600;700&display=swap" rel="stylesheet">
<style>
:root{
  --navy:#1f4190;
  --brand-blue:#2271b3;
  --square-blue:#1f64bf;
  --bar-light:#d5e6ee;
  --field-ink:#3e5566;
  --column-grey:#e0e0e0;
  --panel:#ffffff;
  --ink:#111111;
  --table-label-a:#e9e9ea;
  --table-label-b:#f4f4f5;
  --slate-a:#5e6d7e;
  --slate-b:#6a7a8b;
  --crypto-a:#2f8fd0;
  --crypto-b:#3ba2dd;
  --lynx-a:#2e88cc;
  --lynx-b:#3a9bd8;
  --check-green:#8cc63f;
}
*{box-sizing:border-box;margin:0;padding:0}
html,body{width:1200px;height:2400px;overflow:hidden;background:#fff}
body{font-family:'Poppins',sans-serif;color:var(--ink);position:relative}
.abs{position:absolute}

.top-band{left:0;top:0;width:1200px;height:47px;background:var(--navy)}
.hero-photo{left:0;top:47px;width:1200px;height:337px;
  background:linear-gradient(100deg,#4a5a72 0%,#8a8f99 25%,#c9c4be 45%,#d8dce4 65%,#a8b6cf 85%,#7d93be 100%);opacity:.75}
.hero-squares{left:942px;top:161px;display:flex;gap:14px}
.hero-squares span{width:30px;height:30px;background:var(--square-blue);display:block}
.brand-band{left:0;top:209px;width:1200px;height:148px;background:#fff}
.brand-name{position:absolute;left:108px;top:58px;display:flex;align-items:center;gap:9px;
  font-weight:700;font-size:20px;color:var(--navy)}
.brand-name i{width:20px;height:20px;background:var(--navy);display:block}
.brand-claim{position:absolute;left:288px;top:60px;font-weight:700;font-size:23px;color:var(--navy);letter-spacing:-.3px;white-space:nowrap}

.column-bg{left:178px;top:384px;width:882px;height:2016px;background:var(--column-grey)}
.intro-panel{left:178px;top:417px;width:882px;height:613px;background:var(--panel)}
.intro-title{position:absolute;left:23px;top:22px;font-weight:600;font-size:28px}
.intro-text{position:absolute;left:23px;top:63px;width:840px;font-size:14.6px;line-height:17.5px}

.signup-form{left:178px;top:583px;width:882px;height:360px}
.bar{position:absolute;width:279px;height:48px;display:flex;align-items:center}
.bar.light{background:var(--bar-light)}
.bar.dark{background:var(--brand-blue);color:#fff;padding:0 20px;font-size:14.5px;font-weight:500}
.bar.dark strong{font-weight:700;margin-right:6px}
.bar input[type=text],.bar input[type=email],.bar input[type=tel]{
  width:100%;height:100%;border:0;background:transparent;padding:0 20px;
  font-family:'Poppins',sans-serif;font-size:14.5px;color:var(--ink);outline:none}
.bar input::placeholder{color:var(--field-ink);opacity:1}
.chevron{position:absolute;top:259px}
.chevron-content{position:absolute;top:259px;width:279px;height:48px;display:flex;align-items:center;justify-content:center;
  font-size:13px;color:var(--field-ink);gap:8px}
.chevron-content input{width:15px;height:15px;accent-color:var(--brand-blue)}
.submit-button{position:absolute;left:602px;top:259px;width:279px;height:60px;border:0;background:transparent;
  font-family:'Poppins',sans-serif;font-weight:700;font-size:17px;letter-spacing:.8px;color:#fff;cursor:pointer}

.compare-panel{left:178px;top:1030px;width:882px;height:560px;background:var(--panel);border-top:1px solid #e6e6e6}
.compare-title{position:absolute;left:0;width:100%;top:26px;text-align:center;font-weight:600;font-size:23px}

.compare-table{left:219px;top:1111px;width:829px;display:grid;
  grid-template-columns:274px repeat(4,1fr);grid-auto-rows:43.1px;
  border-radius:0 10px 10px 10px;overflow:hidden;box-shadow:0 6px 10px rgba(0,0,0,.25)}
.compare-table .head{height:45px;display:flex;align-items:center;justify-content:center;text-align:center;
  color:#fff;font-weight:600;font-size:12.5px;line-height:13px;letter-spacing:.4px}
.compare-table .head.corner{background:#f7f7f7}
.c-direct{background:var(--slate-a)}
.c-crypto{background:var(--crypto-a)}
.c-crowd{background:var(--slate-b)}
.c-lynx{background:linear-gradient(180deg,var(--lynx-b),#2a78c6)}
.compare-table .label{display:flex;align-items:center;padding-left:24px;font-weight:600;font-size:13.5px;line-height:15px;letter-spacing:.2px}
.label.odd{background:var(--table-label-a)}
.label.even{background:var(--table-label-b)}
.cell{display:flex;align-items:center;justify-content:center}
.cell svg{width:16px;height:16px}
.d.odd{background:var(--slate-a)} .d.even{background:var(--slate-b)}
.k.odd{background:var(--crypto-a)} .k.even{background:var(--crypto-b)}
.w.odd{background:#5a6a7b} .w.even{background:var(--slate-b)}
.l.odd{background:var(--lynx-a)} .l.even{background:var(--lynx-b)}
.compare-table .r9.l{background:#2369b9}

.zigzag{left:178px;top:1565px}

.closing-photo{left:179px;top:1665px;width:881px;height:460px;
  background:linear-gradient(180deg,#3b4e60 0%,#7c93a6 35%,#526b7d 60%,#1c2a35 100%)}
.closing-veil{left:180px;top:1794px;width:431px;height:298px;background:rgba(255,255,255,.55)}
.closing-brand{left:196px;top:1850px;display:flex;align-items:center;gap:9px;font-weight:700;font-size:20px;color:var(--navy)}
.closing-brand i{width:20px;height:20px;background:var(--navy);display:block}
.closing-headline{left:694px;top:1868px;color:#fff;font-weight:700;font-size:66px;line-height:78px;letter-spacing:-1px}

.footer-band{left:0;top:2155px;width:1200px;height:218px;background:var(--navy)}
</style>
</head>
<body>
<svg width="0" height="0" style="position:absolute">
  <defs>
    <symbol id="tick" viewBox="0 0 16 16"><path d="M2 8.5l4 4L14 4" fill="none" stroke="currentColor" stroke-width="2.2" stroke-linecap="round" stroke-linejoin="round"/></symbol>
    <symbol id="cross" viewBox="0 0 16 16"><path d="M4 4l8 8M12 4l-8 8" fill="none" stroke="currentColor" stroke-width="2.2" stroke-linecap="round"/></symbol>
  </defs>
</svg>

<header>
  <div class="abs top-band"></div>
  <div class="abs hero-photo" role="img" aria-label="Foto: Hände mit Stift über Finanzcharts und Kaffeetasse"></div>
  <div class="abs hero-squares"><span></span><span></span><span></span></div>
  <div class="abs brand-band">
    <div class="brand-name"><i></i>CopperLynx</div>
    <p class="brand-claim">LOREM IPSUM DOLOR SIT AMET, CONSECTETUER ADIPISCING ELIT, SED</p>
  </div>
</header>

<div class="abs column-bg"></div>

<section class="abs intro-panel">
  <h1 class="intro-title">Lorem ipsum</h1>
  <p class="intro-text">Lorem ipsum dolor sit amet, consectetuer adipiscing elit, sed diam nonummy nibh euismod tincidunt ut laoreet dolore magna aliquam erat volutpat. Ut wisi enim ad minim veniam, quis nostrud exerci tation ullamcorper</p>
</section>

<form class="abs signup-form" action="#" method="post" aria-label="Webinar-Anmeldung">
  <label class="bar light" style="left:0;top:0"><input type="text" name="vorname" placeholder="Vorname" aria-label="Vorname"></label>
  <label class="bar light" style="left:301px;top:0"><input type="text" name="nachname" placeholder="Nachname" aria-label="Nachname"></label>
  <div class="bar dark" style="left:602px;top:0"><strong>Kostenloses Webinar</strong></div>

  <label class="bar light" style="left:0;top:65px"><input type="email" name="email" placeholder="E-Mail-Adresse" aria-label="E-Mail-Adresse"></label>
  <label class="bar light" style="left:301px;top:65px"><input type="tel" name="telefon" placeholder="Telefonnummer" aria-label="Telefonnummer"></label>
  <div class="bar dark" style="left:602px;top:65px"><strong>Datum:</strong>Donnerstag, 12.03.</div>

  <label class="bar light" style="left:0;top:130px"><input type="text" name="wohnort" placeholder="Wohnort" aria-label="Wohnort"></label>
  <label class="bar light" style="left:301px;top:130px"><input type="text" name="beruf" placeholder="Beruf" aria-label="Beruf"></label>
  <div class="bar dark" style="left:602px;top:130px"><strong>Uhrzeit:</strong>19:00 Uhr</div>

  <label class="bar light" style="left:0;top:195px"><input type="text" name="alter" placeholder="Alter" aria-label="Alter"></label>
  <label class="bar light" style="left:301px;top:195px"><input type="text" name="quelle" placeholder="Wie haben Sie uns gefunden?" aria-label="Wie haben Sie uns gefunden?"></label>
  <div class="bar dark" style="left:602px;top:195px"><strong>Dauer:</strong>60 Minuten, live</div>

  <svg class="chevron" style="left:0" width="279" height="95" viewBox="0 0 279 95"><path d="M0 0H279V48L139.5 95L0 48Z" fill="var(--bar-light)"/></svg>
  <svg class="chevron" style="left:301px" width="279" height="95" viewBox="0 0 279 95"><path d="M0 0H279V48L139.5 95L0 48Z" fill="var(--bar-light)"/></svg>
  <svg class="chevron" style="left:602px" width="279" height="95" viewBox="0 0 279 95"><path d="M0 0H279V48L139.5 95L0 48Z" fill="var(--brand-blue)"/></svg>

  <label class="chevron-content" style="left:0"><input type="checkbox" name="datenschutz">Datenschutz akzeptiert</label>
  <label class="chevron-content" style="left:301px"><input type="checkbox" name="newsletter">Newsletter erhalten</label>
  <button class="submit-button" type="submit">JETZT ANMELDEN</button>
</form>

<section class="abs compare-panel">
  <h2 class="compare-title">Ihre Vorteile mit Copper Lynx Investments</h2>
</section>

<div class="abs compare-table">
  <div class="head corner"></div>
  <div class="head c-direct">DIREKT<br>INVESTMENTS</div>
  <div class="head c-crypto">KRYPTO<br>INVESTMENTS</div>
  <div class="head c-crowd">CROWDFUNDING</div>
  <div class="head c-lynx">COPPER LYNX<br>INVESTMENTS</div>

  <div class="label odd">Zugang zu KMUs<br>Early Stage Investitionen</div>
  <div class="cell d odd" style="color:#fff"><svg><use href="#tick"/></svg></div>
  <div class="cell k odd" style="color:#fff"><svg><use href="#tick"/></svg></div>
  <div class="cell w odd" style="color:#fff"><svg><use href="#tick"/></svg></div>
  <div class="cell l odd" style="color:var(--check-green)"><svg><use href="#tick"/></svg></div>

  <div class="label even">Geringere Transaktionskosten<br>als klassische Assets</div>
  <div class="cell d even" style="color:#fff"><svg><use href="#cross"/></svg></div>
  <div class="cell k even" style="color:#fff"><svg><use href="#tick"/></svg></div>
  <div class="cell w even" style="color:#fff"><svg><use href="#cross"/></svg></div>
  <div class="cell l even" style="color:var(--check-green)"><svg><use href="#tick"/></svg></div>

  <div class="label odd">Geringes Investment möglich</div>
  <div class="cell d odd" style="color:#fff"><svg><use href="#cross"/></svg></div>
  <div class="cell k odd" style="color:#fff"><svg><use href="#tick"/></svg></div>
  <div class="cell w odd" style="color:#fff"><svg><use href="#tick"/></svg></div>
  <div class="cell l odd" style="color:var(--check-green)"><svg><use href="#tick"/></svg></div>

  <div class="label even">Schnelle Transaktionen</div>
  <div class="cell d even" style="color:#fff"><svg><use href="#cross"/></svg></div>
  <div class="cell k even" style="color:#fff"><svg><use href="#tick"/></svg></div>
  <div class="cell w even" style="color:#fff"><svg><use href="#cross"/></svg></div>
  <div class="cell l even" style="color:var(--check-green)"><svg><use href="#tick"/></svg></div>

  <div class="label odd">Liquidität durch Handelbarkeit</div>
  <div class="cell d odd" style="color:#fff"><svg><use href="#cross"/></svg></div>
  <div class="cell k odd" style="color:#fff"><svg><use href="#tick"/></svg></div>
  <div class="cell w odd" style="color:#fff"><svg><use href="#cross"/></svg></div>
  <div class="cell l odd" style="color:var(--check-green)"><svg><use href="#tick"/></svg></div>

  <div class="label even">Eigentumsanteile</div>
  <div class="cell d even" style="color:#fff"><svg><use href="#tick"/></svg></div>
  <div class="cell k even" style="color:#fff"><svg><use href="#cross"/></svg></div>
  <div class="cell w even" style="color:#fff"><svg><use href="#cross"/></svg></div>
  <div class="cell l even" style="color:var(--check-green)"><svg><use href="#tick"/></svg></div>

  <div class="label odd">Zugang rund um die Uhr</div>
  <div class="cell d odd" style="color:#fff"><svg><use href="#cross"/></svg></div>
  <div class="cell k odd" style="color:#fff"><svg><use href="#tick"/></svg></div>
  <div class="cell w odd" style="color:#fff"><svg><use href="#tick"/></svg></div>
  <div class="cell l odd" style="color:var(--check-green)"><svg><use href="#tick"/></svg></div>

  <div class="label even">Sicherheit durch Regularien</div>
  <div class="cell d even" style="color:#fff"><svg><use href="#tick"/></svg></div>
  <div class="cell k even" style="color:#fff"><svg><use href="#cross"/></svg></div>
  <div class="cell w even" style="color:#fff"><svg><use href="#tick"/></svg></div>
  <div class="cell l even" style="color:var(--check-green)"><svg><use href="#tick"/></svg></div>

  <div class="label odd">Einfacher Zugang</div>
  <div class="cell d odd" style="color:#fff"><svg><use href="#cross"/></svg></div>
  <div class="cell k odd" style="color:#fff"><svg><use href="#tick"/></svg></div>
  <div class="cell w odd" style="color:#fff"><svg><use href="#tick"/></svg></div>
  <div class="cell l odd r9" style="color:var(--check-green)"><svg><use href="#tick"/></svg></div>
</div>

<svg class="abs zigzag" width="882" height="100" viewBox="0 0 882 100">
  <rect x="0" y="0" width="882" height="100" fill="var(--column-grey)"/>
  <path d="M0 0H882V5L736 48L602 5L440 48L301 5L137 48L0 5Z" fill="#fff"/>
</svg>

<section>
  <div class="abs closing-photo" role="img" aria-label="Foto: Geschäftsmann vor Panoramafenster mit digitalen Finanzdaten-Einblendungen"></div>
  <div class="abs closing-veil"></div>
  <div class="abs closing-brand"><i></i>CopperLynx</div>
  <p class="abs closing-headline">Lorem<br>ipsum<br>dolor sit</p>
</section>

<footer class="abs footer-band"></footer>
</body>
</html>
```